Harbourline Physiotherapy business card design

We need a fresh, new business card design for our physiotherapy clinic Harbourline Physiotherapy

Will attach logo soon we had logo designed from our last project

Industry/Entity Type

Physical Therapy

Contact Information for Business Card

On front
Needs our logo, contact details:
58 Wexley Lane St Clair NSW 2759
Ph/f: 02 9481 2057
info@harbourlinephysio.example.com.au

Requirements
Must have
• On the back of the card needs to have area to write down follow up appointments
• On front
• Needs our logo
• The colours have to be the colours in our logo which are: sky blue, black and white
• Font to be same as our logo please
• We want the card to look simple, not too cluttered but to the point
Should not have
• We don't need any extra pictures other than our logo

```html
<!DOCTYPE html>
<html lang="en">
<head>
<meta charset="utf-8">
<title>Harbourline Physiotherapy – Business Card</title>
<link href="https://fonts.googleapis.com/css2?family=Open+Sans:ital,wght@0,400;0,600;0,700;1,400&display=swap" rel="stylesheet">
<style>
  :root {
    --bg: #ecebe8;
    --card-white: #ffffff;
    --sky: #2f8fd8;
    --sky-light: #45b3ec;
    --royal: #3340b0;
    --deep: #24207e;
    --ink: #1c1c1c;
    --grey-swoosh: #4a4a4a;
    --dots: #7ea6d8;
    --text-blue: #2a6fc0;
  }
  * { box-sizing: border-box; margin: 0; padding: 0; }
  html, body { width: 1200px; height: 950px; overflow: hidden; }
  body {
    background: var(--bg);
    font-family: "Open Sans", Arial, sans-serif;
    position: relative;
  }
  .card {
    position: absolute;
    left: 250px;
    width: 700px;
    height: 428px;
    background: var(--card-white);
    border-radius: 4px;
    overflow: hidden;
    box-shadow: 0 6px 18px rgba(0,0,0,0.14);
  }
  .card--front { top: 26px; }
  .card--back { top: 496px; }

  /* Front */
  .front-art { position: absolute; inset: 0; width: 100%; height: 100%; }
  .brand {
    position: absolute;
    top: 52px;
    right: 58px;
    display: flex;
    align-items: center;
    gap: 16px;
  }
  .brand__dot {
    width: 44px; height: 44px;
    border-radius: 50%;
    background: var(--sky);
  }
  .brand__name {
    font-weight: 600;
    font-size: 30px;
    line-height: 1.15;
    color: var(--royal);
    letter-spacing: 0.2px;
  }
  .person {
    position: absolute;
    left: 44px;
    top: 204px;
    color: #fff;
  }
  .person__name { font-size: 24px; font-weight: 700; line-height: 1.2; }
  .person__role { font-size: 16px; font-weight: 400; margin-top: 2px; }
  .contact {
    position: absolute;
    left: 44px;
    top: 278px;
    color: #fff;
    font-size: 14.5px;
    line-height: 1.42;
  }
  .contact__address { margin-bottom: 8px; }
  .contact__row { display: flex; align-items: center; gap: 9px; }
  .contact__row svg { width: 14px; height: 14px; flex: none; }

  /* Back */
  .appointment__title {
    position: absolute;
    top: 46px;
    left: 0; right: 0;
    text-align: center;
    font-size: 30px;
    font-weight: 700;
    color: var(--text-blue);
  }
  .appointment__field {
    position: absolute;
    left: 58px;
    right: 58px;
    display: flex;
    align-items: flex-end;
    gap: 10px;
    color: var(--text-blue);
    font-size: 17px;
  }
  .appointment__field--name { top: 128px; }
  .appointment__field--blank { top: 184px; }
  .appointment__field--time { top: 240px; }
  .appointment__dots {
    flex: 1;
    border-bottom: 2px dotted var(--dots);
    height: 20px;
  }
  .appointment__ampm { font-size: 13px; font-style: italic; }
  .appointment__note {
    position: absolute;
    left: 58px;
    right: 58px;
    bottom: 58px;
    color: var(--text-blue);
    font-size: 15px;
    font-style: italic;
    line-height: 1.5;
  }
</style>
</head>
<body>

<section class="card card--front" aria-label="Business card front">
  <svg class="front-art" viewBox="0 0 700 428" preserveAspectRatio="none" aria-hidden="true">
    <defs>
      <radialGradient id="blueGlow" cx="0.35" cy="0.7" r="0.75">
        <stop offset="0" stop-color="#45b3ec"/>
        <stop offset="0.45" stop-color="#3458c6"/>
        <stop offset="1" stop-color="#24207e"/>
      </radialGradient>
    </defs>
    <path d="M0,150 C210,130 330,300 700,212" fill="none" stroke="#4a4a4a" stroke-width="5" opacity="0.85"/>
    <path d="M0,172 C220,152 360,330 700,236 L700,428 L0,428 Z" fill="url(#blueGlow)"/>
    <path d="M0,172 C220,152 360,330 700,236" fill="none" stroke="#ffffff" stroke-width="4"/>
  </svg>

  <div class="brand">
    <span class="brand__dot"></span>
    <span class="brand__name">Harbourline<br>Physiotherapy</span>
  </div>

  <div class="person">
    <div class="person__name">Daniel Hartley</div>
    <div class="person__role">CEO/Founder</div>
  </div>

  <div class="contact">
    <div class="contact__address">58 Wexley Lane Marlow Vale<br>NSW 2871</div>
    <div class="contact__row">
      <svg viewBox="0 0 16 16" aria-hidden="true"><path fill="#fff" d="M3.5 1.5l2.5 0 1 3.5-1.8 1.2c.8 1.8 2 3 3.8 3.8l1.2-1.8 3.5 1v2.5c0 .8-.7 1.5-1.5 1.5C6.5 13.2 2.8 9.5 2 3c0-.8.7-1.5 1.5-1.5z"/></svg>
      <span>02 9481 2057</span>
    </div>
    <div class="contact__row">
      <svg viewBox="0 0 16 16" aria-hidden="true"><rect x="4" y="1.5" width="8" height="4" fill="none" stroke="#fff" stroke-width="1.4"/><rect x="1.5" y="5.5" width="13" height="6" rx="1" fill="#fff"/><rect x="4" y="10" width="8" height="4.5" fill="#fff" stroke="#2a3aa8" stroke-width="1"/></svg>
      <span>02 9481 2057</span>
    </div>
    <div class="contact__row">
      <svg viewBox="0 0 16 16" aria-hidden="true"><rect x="1.5" y="3.5" width="13" height="9" rx="1" fill="#fff"/><path d="M1.8 4l6.2 5 6.2-5" fill="none" stroke="#2a3aa8" stroke-width="1.3"/></svg>
      <span>info@harbourlinephysio.example.com.au</span>
    </div>
    <div class="contact__row">
      <svg viewBox="0 0 16 16" aria-hidden="true"><circle cx="8" cy="8" r="6.5" fill="none" stroke="#fff" stroke-width="1.4"/><ellipse cx="8" cy="8" rx="2.8" ry="6.5" fill="none" stroke="#fff" stroke-width="1.2"/><path d="M1.5 8h13" stroke="#fff" stroke-width="1.2"/></svg>
      <span>www.harbourlinephysio.example.com.au</span>
    </div>
  </div>
</section>

<section class="card card--back" aria-label="Business card back">
  <h2 class="appointment__title">Next Appointment</h2>
  <div class="appointment__field appointment__field--name">
    <span>Name :</span><span class="appointment__dots"></span>
  </div>
  <div class="appointment__field appointment__field--blank">
    <span class="appointment__dots"></span>
  </div>
  <div class="appointment__field appointment__field--time">
    <span>Time :</span><span class="appointment__dots"></span><span class="appointment__ampm">AM/PM</span>
  </div>
  <p class="appointment__note">Please give 24 hours notice if you are unable to keep your appointment or a cancellation fee may be charged.</p>
</section>

</body>
</html>
```